KLV Plant Services

We are a heavy diesel mechanical business with additional air con certificates, remapping engine rebuilt

Contact Information for Business Card

Company Name, Director Name, Managing Director, Contact details, email and website

Font styles to use
Serif
Script

```html
<!DOCTYPE html>
<html lang="en">
<head>
<meta charset="utf-8">
<title>KLV Plant Services – Business Card</title>
<link rel="stylesheet" href="https://fonts.googleapis.com/css2?family=Montserrat:wght@400;500;700;800&display=swap">
<style>
  :root {
    --stage: #2c2c2e;
    --card-navy: #0c0a78;
    --card-navy-deep: #08065c;
    --ink-white: #ffffff;
    --art-light: #f4f5fb;
    --art-soft: #c9cbe8;
  }
  * { box-sizing: border-box; margin: 0; padding: 0; }
  html, body {
    width: 1200px;
    height: 904px;
    overflow: hidden;
    background: var(--stage);
    font-family: "Montserrat", Arial, sans-serif;
    color: var(--ink-white);
  }
  .canvas {
    position: relative;
    width: 1200px;
    height: 904px;
  }
  .card {
    position: absolute;
    width: 700px;
    height: 400px;
    background: linear-gradient(135deg, var(--card-navy) 0%, var(--card-navy-deep) 100%);
    box-shadow: 0 18px 40px rgba(0,0,0,0.45);
    overflow: hidden;
  }
  .card--front { left: 90px; top: 36px; }
  .card--back  { left: 410px; top: 468px; }

  /* front */
  .brand-lockup {
    position: absolute;
    inset: 0;
    display: flex;
    flex-direction: column;
    align-items: center;
    justify-content: center;
    font-weight: 800;
    line-height: 1;
  }
  .brand-lockup__initials { font-size: 120px; letter-spacing: 2px; }
  .brand-lockup__descriptor { font-size: 38px; margin-top: 10px; }

  /* back */
  .brand-small {
    position: absolute;
    left: 48px; top: 40px;
    font-weight: 800;
    line-height: 1;
  }
  .brand-small__initials { font-size: 54px; display: block; }
  .brand-small__descriptor { font-size: 18px; display: block; margin-top: 4px; }

  .contact-block {
    position: absolute;
    left: 48px; top: 168px;
    width: 380px;
  }
  .person-name {
    font-size: 30px;
    font-weight: 700;
    letter-spacing: 1px;
  }
  .person-role {
    font-size: 16px;
    font-weight: 500;
    letter-spacing: 1px;
    margin-top: 4px;
  }
  .contact-list {
    list-style: none;
    margin-top: 16px;
    font-size: 18px;
    font-weight: 400;
  }
  .contact-list li {
    display: flex;
    align-items: center;
    gap: 12px;
    height: 30px;
  }
  .contact-list svg { width: 18px; height: 18px; flex: none; }
  .address {
    margin-top: 12px;
    font-size: 18px;
    line-height: 1.35;
    padding-left: 30px;
  }

  .excavator-art {
    position: absolute;
    right: 40px;
    top: 0;
    width: 210px;
    height: 340px;
    border-radius: 0 0 90px 40px;
    background: linear-gradient(170deg, var(--art-light) 0%, var(--art-soft) 100%);
  }
</style>
</head>
<body>
<main class="canvas">

  <section class="card card--front" aria-label="Business card front">
    <div class="brand-lockup">
      <span class="brand-lockup__initials">KLV</span>
      <span class="brand-lockup__descriptor">Plant Services</span>
    </div>
  </section>

  <section class="card card--back" aria-label="Business card back">
    <div class="brand-small">
      <span class="brand-small__initials">KLV</span>
      <span class="brand-small__descriptor">Plant Services</span>
    </div>

    <div class="contact-block">
      <h1 class="person-name">MARCUS HALE</h1>
      <p class="person-role">MANAGING DIRECTOR</p>
      <ul class="contact-list">
        <li>
          <svg viewBox="0 0 24 24" aria-hidden="true"><path fill="#fff" d="M6.6 10.8a15 15 0 0 0 6.6 6.6l2.2-2.2a1 1 0 0 1 1-.25 11.4 11.4 0 0 0 3.6.57 1 1 0 0 1 1 1V20a1 1 0 0 1-1 1A17 17 0 0 1 3 4a1 1 0 0 1 1-1h3.5a1 1 0 0 1 1 1c0 1.25.2 2.45.57 3.57a1 1 0 0 1-.25 1z"/></svg>
          041-555 208 317
        </li>
        <li>
          <svg viewBox="0 0 24 24" aria-hidden="true"><rect x="2" y="5" width="20" height="14" rx="1.5" fill="#fff"/><path d="M3 6.5l9 6.5 9-6.5" stroke="#0c0a78" stroke-width="2" fill="none"/></svg>
          hello@klvplant.com
        </li>
        <li>
          <svg viewBox="0 0 24 24" aria-hidden="true"><circle cx="12" cy="12" r="9" fill="none" stroke="#fff" stroke-width="2"/><path d="M3 12h18M12 3c3 3.5 3 14.5 0 18M12 3c-3 3.5-3 14.5 0 18" stroke="#fff" stroke-width="1.6" fill="none"/></svg>
          www.klvplant.com
        </li>
      </ul>
      <p class="address">18 Quarry Road, Brookvale<br>2100, Australia</p>
    </div>

    <div class="excavator-art" role="img" aria-label="Large white excavator arm and bucket illustration"></div>
  </section>

</main>
</body>
</html>
```